QVR business card

Need a business card for a company that provides instructional design and elearning development services. The website is here: http://quorvane.studio/

I'm attaching a current logo, as well as the old business card design. While I like to keep it clean, the old design is too simplistic for my liking. The only idea I want to reuse from the old design is placing industry jargon on the back of the card, just need a better way to present it. But if you have other ideas for the back--feel free to experiment.

Please use the colors complementary to the color we have on the website. Thank you!

```html
<!DOCTYPE html>
<html lang="en">
<head>
<meta charset="utf-8">
<title>QVR business card</title>
<link rel="stylesheet" href="https://fonts.googleapis.com/css2?family=Open+Sans:wght@400;600&family=Arimo:wght@700&display=swap">
<style>
  :root {
    --teal: #1fb1ac;
    --teal-soft: #3bb8ae;
    --sand: #d9cf93;
    --sand-light: #dcd3a0;
    --gold-text: #d4c887;
    --ink: #2b2b2b;
    --white: #ffffff;
    --backdrop: #b9b9b9;
  }
  * { box-sizing: border-box; margin: 0; padding: 0; }
  html, body { width: 1200px; height: 1080px; overflow: hidden; }
  body {
    background: var(--backdrop);
    font-family: "Open Sans", sans-serif;
    position: relative;
  }
  .card {
    position: absolute;
    width: 700px;
    height: 400px;
    overflow: hidden;
    box-shadow: 0 10px 24px rgba(0,0,0,0.25);
  }

  /* Back side */
  .card-back {
    left: 70px; top: 80px;
    background: linear-gradient(180deg, var(--teal-soft) 0%, #79bba6 45%, var(--sand-light) 100%);
  }
  .card-back .brand-name {
    position: absolute; top: 58px; left: 0; width: 100%;
    text-align: center;
    font-size: 64px; font-weight: 600; letter-spacing: 4px;
    color: var(--white);
  }
  .card-back .world-map {
    position: absolute; left: 110px; top: 150px;
    width: 480px; height: 200px;
    border-radius: 40px;
    background: radial-gradient(ellipse at center, rgba(31,150,140,0.35) 0%, rgba(31,150,140,0.12) 60%, rgba(31,150,140,0) 100%);
  }
  .services {
    position: absolute; top: 178px; left: 0; width: 100%;
    display: flex; flex-direction: column; align-items: center; gap: 4px;
  }
  .service-tag {
    background: var(--teal);
    color: var(--white);
    font-size: 22px;
    line-height: 30px;
    padding: 0 10px;
    border-radius: 3px;
  }
  .card-back .site {
    position: absolute; bottom: 40px; left: 0; width: 100%;
    text-align: center; color: var(--white); font-size: 18px;
  }

  /* Front side */
  .card-front {
    left: 430px; top: 600px;
    background: var(--white);
  }
  .logo {
    position: absolute; left: 44px; top: 52px;
    display: flex; align-items: center; gap: 14px;
  }
  .logo-dot {
    width: 40px; height: 40px; border-radius: 50%;
    background: var(--teal);
  }
  .logo-name {
    font-size: 52px; font-weight: 600; letter-spacing: 3px;
    color: var(--teal);
  }
  .contact-panel {
    position: absolute; left: 330px; top: 232px;
    width: 370px; height: 136px;
    background: var(--sand);
  }
  .name-band {
    position: absolute; left: 0; top: 212px;
    width: 380px; height: 112px;
    background: var(--teal);
  }
  .person {
    position: absolute; left: 50px; top: 28px;
    text-align: center;
  }
  .person-name {
    font-family: "Arimo", sans-serif;
    font-weight: 700; font-size: 24px;
    color: var(--gold-text);
  }
  .person-role { font-size: 19px; color: var(--ink); }
  .contact-icons {
    position: absolute; right: 10px; top: 22px;
    display: flex; flex-direction: column; gap: 8px;
  }
  .contact-icons svg { width: 20px; height: 20px; display: block; }
  .contact-list {
    position: absolute; left: 400px; top: 256px;
    list-style: none;
    font-size: 20px; line-height: 30px; color: var(--ink);
  }
</style>
</head>
<body>

  <section class="card card-back" aria-label="Card back">
    <div class="brand-name">QVR</div>
    <div class="world-map" role="img" aria-label="Dotted world map"></div>
    <div class="services">
      <span class="service-tag">Instructional Design</span>
      <span class="service-tag">Elearning Development | Mobile Learning</span>
      <span class="service-tag">Insructor-LED Training</span>
    </div>
    <div class="site">www.quorvane.studio</div>
  </section>

  <section class="card card-front" aria-label="Card front">
    <div class="logo">
      <span class="logo-dot"></span>
      <span class="logo-name">QVR</span>
    </div>

    <div class="contact-panel"></div>

    <div class="name-band">
      <div class="person">
        <div class="person-name">Daniel Marsh</div>
        <div class="person-role">managing director</div>
      </div>
      <div class="contact-icons">
        <svg viewBox="0 0 20 20" aria-label="Phone"><path fill="#d9cf93" d="M3 7c0-2 2-3 7-3s7 1 7 3v1h-4V6.5c-1-.4-5-.4-6 0V8H3zM5 9h10l2 7H3z"/></svg>
        <svg viewBox="0 0 20 20" aria-label="Email"><rect x="2" y="5" width="16" height="11" fill="#d9cf93"/><path d="M2 5l8 6 8-6" fill="none" stroke="#1fb1ac" stroke-width="1.5"/></svg>
        <svg viewBox="0 0 20 20" aria-label="Website"><circle cx="10" cy="10" r="8" fill="none" stroke="#d9cf93" stroke-width="1.6"/><ellipse cx="10" cy="10" rx="3.5" ry="8" fill="none" stroke="#d9cf93" stroke-width="1.4"/><path d="M2 10h16M4 6h12M4 14h12" stroke="#d9cf93" stroke-width="1.2"/></svg>
      </div>
    </div>

    <ul class="contact-list">
      <li>555-014-2290</li>
      <li>dmarsh@quorvane.studio</li>
      <li>www.quorvane.studio</li>
    </ul>
  </section>

</body>
</html>
```